Wheels for Heroes Website Design

We need a NEW design and uploaded to Hostrova.com. Here is the current site: http://www.wheelsforheroes.org

Need a form like this:

https://youthautogifts.org/

Coding

Coded - Design and coding required

Number of Pages Required

1 page

```html
<!DOCTYPE html>
<html lang="en">
<head>
<meta charset="utf-8">
<title>Wheels for Heroes – Car Donation</title>
<link href="https://fonts.googleapis.com/css2?family=Lato:wght@400;700;900&display=swap" rel="stylesheet">
<style>
:root{
  --red:#d7141a;
  --navy:#14237e;
  --blue:#1e3a9e;
  --ink:#2b2b2b;
  --muted:#6b6b6b;
  --line:#cfd3da;
  --pale:#eef1f5;
  --dark:#232323;
  --white:#fff;
}
*{box-sizing:border-box;margin:0;padding:0}
html,body{width:1200px;height:3484px;overflow:hidden}
body{font-family:'Lato',sans-serif;color:var(--ink);background:var(--white);position:relative}
.wrap{width:978px;margin:0 auto;position:relative;height:100%}
a{color:inherit;text-decoration:none}

/* header */
.site-header{height:116px;position:relative}
.brand{position:absolute;left:0;top:28px;display:flex;align-items:center;gap:12px;white-space:nowrap}
.brand-dot{width:40px;height:40px;border-radius:50%;background:var(--red);flex:none}
.brand-name{font-weight:900;font-size:28px;color:var(--red);text-transform:uppercase;letter-spacing:.5px}
.call{position:absolute;right:0;top:12px;font-size:18px;display:flex;align-items:center;gap:8px}
.call strong{color:var(--red);font-size:23px;font-weight:900}
.nav{position:absolute;right:0;top:46px;display:flex;align-items:center;gap:22px;font-size:18px}
.btn-red{background:var(--red);color:var(--white);font-weight:900;text-transform:uppercase;display:inline-flex;align-items:center;justify-content:center;border-radius:3px}
.nav .btn-red{height:58px;padding:0 20px;font-size:19px;margin-left:2px}

/* hero */
.hero{height:586px;position:relative;background:linear-gradient(110deg,#3a2c22 0%,#8a6640 35%,#c99a5e 55%,#5c4a36 80%,#2a241e 100%)}
.hero-photo{position:absolute;inset:0}
.hero-copy{position:absolute;left:0;top:140px;color:var(--white)}
.hero-copy h1{font-size:64px;line-height:70px;font-weight:700}
.hero-copy p{font-size:29px;margin-top:16px}
.hero-copy .btn-white{display:inline-flex;margin-top:26px;background:var(--white);color:var(--ink);font-weight:900;font-size:18px;height:64px;padding:0 25px;align-items:center;border-radius:3px}
.donate-card{position:absolute;right:0;top:37px;width:461px;height:483px;background:var(--white);border-radius:5px;padding:22px 24px}
.steps{display:flex;align-items:center;justify-content:center;gap:12px;font-size:19px}
.step-num{width:36px;height:36px;border-radius:50%;display:inline-flex;align-items:center;justify-content:center;color:var(--white);font-weight:700;background:var(--navy)}
.step.off .step-num{background:#b8bcc4}
.step{display:flex;align-items:center;gap:12px;color:var(--navy);font-weight:700}
.step.off{color:#a4a8b0;font-weight:400}
.step-line{width:40px;height:1px;background:var(--line)}
.field-label{font-size:18px;margin-top:34px}
.row{display:flex;margin-top:14px}
.sel{flex:1;height:41px;border:1px solid var(--line);margin-left:-1px;font-size:14px;color:#888;padding:0 12px;display:flex;align-items:center;justify-content:space-between}
.sel:first-child{margin-left:0}
.labels3{display:flex;justify-content:space-between;font-size:18px;margin-top:26px}
.trust{display:flex;justify-content:center;gap:20px;margin-top:34px}
.trust span{width:44px;height:44px;border-radius:50%}
.donate-card .btn-red{display:flex;width:310px;height:64px;margin:28px auto 0;font-size:19px}

/* how */
.how{height:468px;text-align:center;padding-top:42px}
.section-title{font-size:41px;font-weight:400}
.how-grid{display:flex;justify-content:space-between;margin-top:18px}
.how-item{width:340px}
.how-icon{height:140px;display:flex;align-items:center;justify-content:center}
.how-art{width:120px;height:130px;border-radius:8px;background:linear-gradient(135deg,#e3e7f2,#f6e1e2)}
.num{width:44px;height:44px;border:2px solid #777;border-radius:50%;display:inline-flex;align-items:center;justify-content:center;font-size:22px;font-weight:700;margin-top:28px;color:#555}
.how-item h3{font-size:27px;font-weight:400;margin-top:8px}
.how-item p{font-size:16px;color:var(--muted);line-height:30px;margin-top:14px;white-space:nowrap}

/* impact */
.impact{height:567px;background:var(--pale);text-align:center;padding-top:42px}
.cards{display:flex;justify-content:space-between;margin-top:36px}
.card{width:312px;height:383px;background:var(--white);border:1px solid #dde1e6;padding:6px}
.card-photo{height:183px}
.card h3{font-size:26px;font-weight:400;margin-top:22px}
.card p{font-size:16px;color:var(--muted);line-height:28px;margin-top:10px}
.card a{display:block;color:var(--red);font-weight:900;font-size:17px;margin-top:8px}

/* why */
.why{height:581px;background:linear-gradient(135deg,#2540a8,#1c3390 60%,#22399c);color:var(--white);padding-top:44px}
.why .section-title{text-align:center;font-weight:700;font-size:41px}
.why-grid{display:grid;grid-template-columns:328px 366px 320px;row-gap:14px;margin-top:16px}
.why-item svg{height:76px;display:block}
.why-item h3{font-size:23px;font-weight:700;margin-top:16px}
.why-item p{font-size:16px;line-height:28px;margin-top:6px;white-space:nowrap}

/* faq */
.faq{height:742px;text-align:center;padding-top:48px}
.faq-list{width:864px;margin:34px auto 0;text-align:left}
.faq-item{border:2px solid #ccd0d8;border-radius:3px;margin-bottom:13px;padding:0 30px}
.faq-q{height:51px;display:flex;align-items:center;justify-content:space-between;font-size:22px}
.faq-item.open .faq-q{height:66px}
.faq-a{font-size:16px;color:var(--muted);line-height:27px;padding-bottom:18px;padding-right:80px}

/* footer */
.site-footer{height:424px;background:var(--dark);color:var(--white);padding-top:52px}
.foot-cols{display:flex;justify-content:space-between}
.foot-about{width:360px}
.foot-about .brand{position:static}
.foot-about .brand-name{font-size:25px}
.foot-about p{font-size:16px;line-height:28px;margin-top:24px}
.foot-call{text-align:center;width:380px;padding-top:22px}
.foot-call .small{font-size:19px}
.foot-call .big{font-size:35px;font-weight:900;margin-top:10px;display:flex;justify-content:center;align-items:center;gap:10px}
.foot-call .ops{font-size:19px;margin-top:18px}
.badges{display:flex;justify-content:center;gap:30px;margin-top:20px}
.badges span{display:block;height:44px;background:#555;border-radius:4px}
.links{width:185px}
.links h4{font-size:22px;font-weight:700}
.links li{list-style:none;font-size:16px;line-height:28px}
.links ul{margin-top:10px}
.foot-bottom{border-top:1px solid #555;margin-top:28px;padding-top:26px;display:flex;justify-content:space-between;align-items:center;font-size:15px}
.social{display:flex;gap:10px}
.social span{width:44px;height:44px;border:2px solid var(--white);border-radius:50%}
</style>
</head>
<body>

<header class="site-header">
  <div class="wrap">
    <a class="brand" href="#"><span class="brand-dot"></span><span class="brand-name">Wheels for Heroes</span></a>
    <div class="call">
      <svg width="16" height="16" viewBox="0 0 24 24"><path fill="#d7141a" d="M6.6 10.8a15 15 0 006.6 6.6l2.2-2.2a1 1 0 011-.25 11.4 11.4 0 003.6.6 1 1 0 011 1V20a1 1 0 01-1 1A17 17 0 013 4a1 1 0 011-1h3.5a1 1 0 011 1 11.4 11.4 0 00.6 3.6 1 1 0 01-.25 1z"/></svg>
      Call Today to Donate <strong>1-888-555-0147</strong>
    </div>
    <nav class="nav">
      <a href="#">About</a><a href="#">How to Donate</a><a href="#">Wy Donate</a><a href="#">FAQs</a><a href="#">Contact</a>
      <a class="btn-red" href="#">Donate a Car</a>
    </nav>
  </div>
</header>

<section class="hero">
  <div class="hero-photo" role="img" aria-label="Soldier walking hand in hand with family through a sunlit field"></div>
  <div class="wrap">
    <div class="hero-copy">
      <h1>Car Donation<br>Made Easy</h1>
      <p>Join our 500,000+ donors</p>
      <a class="btn-white" href="#">JOIN US NOW!</a>
    </div>
    <form class="donate-card">
      <div class="steps">
        <div class="step"><span class="step-num">1</span>Vehicle info</div>
        <span class="step-line"></span>
        <div class="step off"><span class="step-num">2</span>Contact Info</div>
      </div>
      <div class="field-label">What kind of car?</div>
      <div class="row"><div class="sel">Year<span>⌄</span></div><div class="sel">Make<span>⌄</span></div><div class="sel">Model<span>⌄</span></div></div>
      <div class="labels3"><span>Mileage</span><span>Does It Run?</span><span>Title Available?</span></div>
      <div class="row"><div class="sel">Enter Mileage</div><div class="sel">Select<span>⌄</span></div><div class="sel">Select<span>⌄</span></div></div>
      <div class="trust"><span style="background:#f39237"></span><span style="background:#aab0b8"></span><span style="background:#1aa59a"></span></div>
      <a class="btn-red" href="#">Donate My Vehicle Now!</a>
    </form>
  </div>
</section>

<section class="how">
  <div class="wrap">
    <h2 class="section-title">How to Donate</h2>
    <div class="how-grid">
      <div class="how-item">
        <div class="how-icon"><div class="how-art" role="img" aria-label="Illustration of a form being filled in with a pencil"></div></div>
        <span class="num">1</span>
        <h3>Contact Us</h3>
        <p>Call us at 1-800-555-0192 or<br>Fill out the online form</p>
      </div>
      <div class="how-item">
        <div class="how-icon"><div class="how-art" style="width:150px" role="img" aria-label="Illustration of a hand handing over car keys"></div></div>
        <span class="num">2</span>
        <h3>Schedule Pickup</h3>
        <p>We'll call you today to arrange a convenient<br>pickup time for your car donation.</p>
      </div>
      <div class="how-item">
        <div class="how-icon"><div class="how-art" role="img" aria-label="Illustration of scissors cutting a tax label"></div></div>
        <span class="num">3</span>
        <h3>Tax Deduction</h3>
        <p>You receive a tax receipt and<br>vacation voucher</p>
      </div>
    </div>
  </div>
</section>

<section class="impact">
  <div class="wrap">
    <h2 class="section-title">Your Car Impacts Veterans' Lives</h2>
    <div class="cards">
      <div class="card">
        <div class="card-photo" role="img" aria-label="Soldier with his family in front of their home" style="background:linear-gradient(135deg,#8f7b66,#b7a690,#6c6458)"></div>
        <h3>Help Us Reach Our Goal</h3>
        <p>Sed ut perspiciatis unde omnis is<br>te natus error sit voluptatem accusan<br>tium doloremque laudanti</p>
        <a href="#">JOIN US</a>
      </div>
      <div class="card">
        <div class="card-photo" role="img" aria-label="Smiling young woman leaning on an orange car" style="background:linear-gradient(135deg,#6f9fc4,#a9c6db,#d96d2e)"></div>
        <h3>Vision</h3>
        <p>Sed ut perspiciatis unde omnis is<br>te natus error sit voluptatem accusan<br>tium doloremque laudanti</p>
        <a href="#">ABOUT US</a>
      </div>
      <div class="card">
        <div class="card-photo" role="img" aria-label="Team stacking hands together" style="background:linear-gradient(135deg,#5c3a2e,#a26e55,#3c3330)"></div>
        <h3>On The Field</h3>
        <p>Sed ut perspiciatis unde omnis is<br>te natus error sit voluptatem accusan<br>tium doloremque laudanti</p>
        <a href="#">VOLUNTEER</a>
      </div>
    </div>
  </div>
</section>

<section class="why" role="img" aria-label="Blue-tinted street scene with a parked car">
  <div class="wrap">
    <h2 class="section-title">Why Donate Your Car To Us</h2>
    <div class="why-grid">
      <div class="why-item">
        <svg width="76" viewBox="0 0 76 76" fill="none" stroke="#fff" stroke-width="3"><circle cx="38" cy="38" r="34"/><text x="38" y="45" fill="#fff" stroke="none" font-size="20" font-weight="700" text-anchor="middle" font-family="Lato,sans-serif">24/7</text></svg>
        <h3>IRS 501(c)3 Approved</h3>
        <p>Free 24/7 Pickup with No<br>DMV Hassles</p>
      </div>
      <div class="why-item">
        <svg width="110" viewBox="0 0 110 76" fill="none" stroke="#fff" stroke-width="3"><path d="M4 50l14-30h20l10 20h50v14H4z"/><circle cx="30" cy="60" r="8"/><circle cx="80" cy="60" r="8"/><path d="M60 40V26h20"/></svg>
        <h3>Free Local Towing</h3>
        <p>We will pick up your car donation,running<br>or not, when it's most convenient, at<br>home or work</p>
      </div>
      <div class="why-item">
        <svg width="80" viewBox="0 0 80 76" fill="none" stroke="#fff" stroke-width="3"><circle cx="14" cy="58" r="12"/><path d="M30 74V50h8v24M44 74V38h8v36M58 74V26h8v48"/><circle cx="58" cy="14" r="12"/></svg>
        <h3>Income Tax Deduction</h3>
        <p>We issue you an IRS tax receipt and get<br>you the highest tax write-off possible.</p>
      </div>
      <div class="why-item">
        <svg width="66" viewBox="0 0 66 76" fill="none" stroke="#fff" stroke-width="3"><path d="M8 12h40v60H8zM16 4h40v60M18 26h22M18 36h22M18 46h22"/></svg>
        <h3>No Paperwork Hassles</h3>
        <p>We handle everything: DMV and IRS<br>paperwork</p>
      </div>
      <div class="why-item">
        <svg width="82" viewBox="0 0 82 76" fill="none" stroke="#fff" stroke-width="3"><path d="M4 60V42l12-26h50l12 26v18z"/><path d="M4 42h74M16 52h10M56 52h10"/><path d="M10 60v10h12V60M60 60v10h12V60"/></svg>
        <h3>Car donations help benefit</h3>
        <p>An IRS 501(c)3 nonprofit organization</p>
      </div>
      <div class="why-item">
        <svg width="84" viewBox="0 0 84 76" fill="none" stroke="#fff" stroke-width="3"><path d="M14 10h66v56H14zM14 24h66M28 4v12M66 4v12M26 34h44v20H26zM40 34v20M54 34v20M26 44h44"/><circle cx="14" cy="62" r="11"/></svg>
        <h3>Schedule a Free Pickup</h3>
        <p>Complete the form and a representative<br>will call you to arrange a convenient time<br>to pickup your car.</p>
      </div>
    </div>
  </div>
</section>

<section class="faq">
  <div class="wrap">
    <h2 class="section-title">Frequently Asked Questions</h2>
    <div class="faq-list">
      <div class="faq-item open">
        <div class="faq-q">What types of vehicles can be donated?<span>︿</span></div>
        <div class="faq-a">Nemo enim ipsam voluptatem quia voluptas sit aspernatur aut odit aut fugit, sed quia consequuntur magni dolores eos qui ratione voluptat eque porro quisquam est, qui.</div>
      </div>
      <div class="faq-item"><div class="faq-q">hat paperwork do I need to donate my vehicle?<span>﹀</span></div></div>
      <div class="faq-item"><div class="faq-q">Is my donated vehicle tax-deductible?<span>﹀</span></div></div>
      <div class="faq-item"><div class="faq-q">What if the vehicle is not registered in my name?<span>﹀</span></div></div>
      <div class="faq-item"><div class="faq-q">How much will I receive as a tax deduction for my vehicle?<span>﹀</span></div></div>
      <div class="faq-item"><div class="faq-q">When will I receive my tax receipt?<span>﹀</span></div></div>
      <div class="faq-item"><div class="faq-q">How do I schedule a pick up?<span>﹀</span></div></div>
    </div>
  </div>
</section>

<footer class="site-footer">
  <div class="wrap">
    <div class="foot-cols">
      <div class="foot-about">
        <a class="brand" href="#"><span class="brand-dot"></span><span class="brand-name">Wheels for Heroes</span></a>
        <p>Offers support and/or financial assistance to veterans and active military personal and/or their family members who become newly blind and/or visually impaired from age-related macular degeneration, retinitis pigmentosa, glaucoma, keratoconus or diabetic retinopathy.</p>
      </div>
      <div class="foot-call">
        <div class="small">Call Today To Donate</div>
        <div class="big"><svg width="28" height="28" viewBox="0 0 24 24"><path fill="#fff" d="M6.6 10.8a15 15 0 006.6 6.6l2.2-2.2a1 1 0 011-.25 11.4 11.4 0 003.6.6 1 1 0 011 1V20a1 1 0 01-1 1A17 17 0 013 4a1 1 0 011-1h3.5a1 1 0 011 1 11.4 11.4 0 00.6 3.6 1 1 0 01-.25 1z"/></svg>1-800-555-0192</div>
        <div class="ops">Live Operators Available - 7 Days A Week</div>
        <div class="badges"><span style="width:104px"></span><span style="width:60px;border-radius:50%;background:#6e8bb5"></span></div>
      </div>
      <div class="links">
        <h4>Quick Links</h4>
        <ul><li>How To Donate</li><li>Why Donate</li><li>FAQ</li><li>About</li></ul>
      </div>
    </div>
    <div class="foot-bottom">
      <span>Copyright ©2020. WHEELS FOR HEROES. All rights reserved.</span>
      <div class="social"><span></span><span></span><span></span><span></span></div>
    </div>
  </div>
</footer>

</body>
</html>
```